I need a header for the web site www.halvertonpipeworks.com/demo
It must include the following
Existig Logo (I will upload the .png)
Text: Serving Calgary and Surrounding Areas for Over 30 Years!
24 Hour Service
Call 587.214.7093 (Note this isn't the actual phone number I will need to be able to change the Phone number once the site is ready to put in a tracking number so I am hoping I get a PSD file with this where the text is editable)
We wnat the feel to be warm and geared more towards a residential customer rather than an industial customer.
We would like blue tones but are open to anything warm.

Size: Aprroximately 960x300

Residential

Requirements
Must have
• Rounded Corners to match the content area on the site

```html
<!DOCTYPE html>
<html lang="en">
<head>
<meta charset="utf-8">
<title>Halverton Pipeworks Ltd</title>
<link rel="stylesheet" href="https://fonts.googleapis.com/css2?family=Open+Sans:wght@400;700&family=Noto+Serif:ital,wght@0,400;1,400&display=swap">
<style>
  :root {
    --page-bg: #7d9aa4;
    --topbar: #2b4a5e;
    --topbar-edge: #3c5d72;
    --search-bg: #1f3a4c;
    --white: #ffffff;
    --ink: #333333;
    --navy: #22354e;
    --service-blue: #9eb1c8;
    --tag-grey: #dcdcdc;
    --accent-red: #b1432b;
    --photo-dark: #3a3d40;
    --caption-bg: rgba(25, 25, 25, 0.62);
    --gold: #e6c26a;
    --rule: #e4e4e4;
    --widget-bar: #eef0f0;
  }
  * { margin: 0; padding: 0; box-sizing: border-box; }
  html, body { width: 1200px; height: 929px; overflow: hidden; }
  body {
    position: relative;
    background: var(--page-bg);
    font-family: "Open Sans", sans-serif;
    color: var(--ink);
  }
  .top-bar {
    position: absolute; left: 0; top: 0; width: 1200px; height: 47px;
    background: var(--topbar);
    border-top: 6px solid var(--topbar-edge);
  }
  .top-rule {
    position: absolute; left: 0; top: 54px; width: 1200px;
    border-top: 1px dashed rgba(255,255,255,0.7);
  }
  .search {
    position: absolute; left: 871px; top: 11px; width: 170px; height: 27px;
    background: var(--search-bg); border-radius: 4px;
    border: 1px solid #18303f;
    font-size: 11px; color: #7e93a2; padding: 6px 14px;
  }
  .search svg { position: absolute; right: 10px; top: 6px; }

  /* header */
  .header {
    position: absolute; left: 112px; top: 78px; width: 978px; height: 229px;
    border: 2px solid var(--white); border-radius: 9px; overflow: hidden;
    background: var(--white);
  }
  .logo-zone {
    position: absolute; left: 0; top: 0; width: 421px; height: 80px; background: var(--white);
    display: flex; align-items: center; justify-content: center; gap: 10px;
  }
  .logo-mark { width: 14px; height: 14px; background: var(--navy); border-radius: 50%; }
  .logo-name {
    font-family: "Noto Serif", serif; font-size: 20px; letter-spacing: 2px; color: var(--navy);
  }
  .photo-sink {
    position: absolute; left: 0; top: 80px; width: 421px; height: 145px;
    background: linear-gradient(160deg, #cfd8dc 0%, #e9eeee 45%, #3a3e44 100%);
  }
  .photo-tub {
    position: absolute; left: 421px; top: 0; width: 553px; height: 155px;
    background: linear-gradient(120deg, #8d8e8f 0%, #2d3743 45%, #b7b2aa 100%);
  }
  .service {
    position: absolute; left: 421px; top: 155px; width: 230px; height: 70px;
    background: var(--service-blue); padding: 10px 0 0 20px;
  }
  .service-label { font-family: "Noto Serif", serif; color: var(--white); font-size: 17px; }
  .service-phone { font-family: "Noto Serif", serif; color: var(--navy); font-size: 32px; line-height: 1.15; }
  .tagline {
    position: absolute; left: 651px; top: 155px; width: 323px; height: 70px;
    background: var(--tag-grey);
  }
  .tagline-text {
    position: absolute; right: 86px; top: 16px; text-align: right;
    font-family: "Noto Serif", serif; font-style: italic; color: #3b3b3b;
  }
  .tagline-text .line1 { font-size: 21px; line-height: 1.1; }
  .tagline-text .line2 { font-size: 16px; }
  .tagline-years {
    position: absolute; right: 14px; top: 3px; text-align: center;
    font-family: "Noto Serif", serif; font-style: italic; color: var(--accent-red);
  }
  .tagline-years .num { font-size: 42px; line-height: 1; }
  .tagline-years .word { font-size: 19px; line-height: 1; }

  /* content */
  .content {
    position: absolute; left: 112px; top: 327px; width: 978px; height: 602px;
    background: var(--white); border-radius: 9px 9px 0 0;
  }
  .nav {
    height: 66px; display: flex; padding-left: 29px;
    background: repeating-linear-gradient(135deg, #fafafa 0 2px, #f3f3f3 2px 4px);
    border-radius: 9px 9px 0 0;
  }
  .nav a {
    text-decoration: none; color: #3a3a3a; font-weight: 700; font-size: 13px;
    padding: 0 17px; line-height: 66px; border-right: 1px solid var(--rule);
  }
  .nav a:last-child { border-right: 1px solid var(--rule); }
  .slider {
    position: absolute; left: 0; top: 66px; width: 978px; height: 345px;
    background: linear-gradient(90deg, #5a6470 0%, #8d8f8c 35%, #3b3f44 60%, #6f7a80 100%);
  }
  .caption {
    position: absolute; left: 520px; top: 41px; width: 405px; height: 268px;
    background: var(--caption-bg); border-radius: 9px; padding: 28px 32px 0 32px; color: #ddd;
  }
  .caption-meta { font-family: "Noto Serif", serif; font-style: italic; font-size: 12px; color: #8a8a8a; }
  .caption-meta b { color: var(--white); }
  .caption-title { font-family: "Noto Serif", serif; color: var(--white); font-size: 27px; font-weight: 400; margin: 6px 0 8px; }
  .caption-body { font-size: 11.5px; line-height: 19px; }
  .read-more {
    position: absolute; right: 0; bottom: 0; padding: 6px 16px;
    background: rgba(0,0,0,0.45); color: var(--gold); font-size: 12px; border-radius: 9px 0 9px 0;
  }
  .pointer { position: absolute; left: 299px; top: 401px; }
  .arrow {
    position: absolute; top: 544px; width: 48px; height: 68px; background: var(--white);
    border-radius: 34px; box-shadow: 0 0 4px rgba(0,0,0,.25);
  }
  .arrow svg { position: absolute; top: 27px; }
  .arrow-prev { left: 79px; } .arrow-prev svg { left: 12px; }
  .arrow-next { left: 1074px; } .arrow-next svg { left: 24px; }
  .thumbs { position: absolute; left: 25px; top: 433px; display: flex; gap: 21px; }
  .thumb { width: 97px; height: 55px; border: 1px solid #999; }
  .thumb.active { box-shadow: 0 0 6px rgba(0,0,0,.6); }
  .widgets {
    position: absolute; left: 0; top: 517px; width: 972px; height: 85px; display: flex;
  }
  .widget { flex: 1; border-right: 1px solid var(--rule); }
  .widget h3 {
    height: 40px; line-height: 40px; text-align: center; font-size: 12px; font-weight: 700;
    background: var(--widget-bar); border-bottom: 1px solid var(--rule); border-top: 1px solid var(--rule);
  }
</style>
</head>
<body>
  <div class="top-bar"></div>
  <div class="top-rule"></div>
  <div class="search">search this site...
    <svg width="13" height="13" viewBox="0 0 13 13"><circle cx="7.5" cy="5.5" r="4" fill="none" stroke="#fff" stroke-width="2"/><line x1="4.5" y1="8.5" x2="1" y2="12" stroke="#fff" stroke-width="2.4"/></svg>
  </div>

  <header class="header">
    <div class="logo-zone"><span class="logo-mark"></span><span class="logo-name">HALVERTON PIPEWORKS</span></div>
    <div class="photo-sink" role="img" aria-label="White vessel sink with drain snake on a dark counter"></div>
    <div class="photo-tub" role="img" aria-label="Polished stone bathtub in a tiled bathroom"></div>
    <div class="service">
      <div class="service-label">24 Hour Service</div>
      <div class="service-phone">587.214.7093</div>
    </div>
    <div class="tagline">
      <div class="tagline-text">
        <div class="line1">Serving Calgary &amp;</div>
        <div class="line2">Surrounding Areas for Over</div>
      </div>
      <div class="tagline-years"><div class="num">30</div><div class="word">years!</div></div>
    </div>
  </header>

  <main class="content">
    <nav class="nav">
      <a href="#">HOME</a><a href="#">ABOUT US</a><a href="#">PRODUCT REVIEWS</a><a href="#">LINKS</a><a href="#">ARTICLES »</a><a href="#">CONTACT US</a><a href="#">EMPLOYEE LOGIN</a>
    </nav>
    <section class="slider" role="img" aria-label="Boiler room with water heaters and piping">
      <div class="caption">
        <div class="caption-meta">Posted by <b>admin</b> on Sep 15, 2010</div>
        <h2 class="caption-title">No Job too Big or Small</h2>
        <p class="caption-body">Mauris suscipit porta commodo. Pellentesque mattis interdum nibh sit amet sodales. Curabitur euismod sem in dui cursus et faucibus leo dignissim. Integer non porttitor leo. Integer luctus adipiscing dui nec tempor. Pellentesque convallis ullamcorper dui ornare mattis. Class aptent taciti sociosqu ad litora torquent per conubia nostra, per inceptos himenaeos. Donec tincidunt urna in est sodales tempor....</p>
        <div class="read-more">Read More</div>
      </div>
    </section>
    <svg class="pointer" width="22" height="11" viewBox="0 0 22 11"><polygon points="0,11 11,0 22,11" fill="#fff"/></svg>
    <div class="thumbs">
      <div class="thumb" role="img" aria-label="Freestanding tub" style="background:linear-gradient(#6b5a4c,#d9d6d0)"></div>
      <div class="thumb" role="img" aria-label="Radiant floor tubing" style="background:linear-gradient(#8a5a3e,#b98a6a)"></div>
      <div class="thumb active" role="img" aria-label="Boiler room" style="background:linear-gradient(90deg,#5a6470,#9aa0a2)"></div>
      <div class="thumb" role="img" aria-label="Mechanical piping" style="background:linear-gradient(#7a6a5c,#c9c2b8)"></div>
      <div class="thumb" role="img" aria-label="Glass vessel sink" style="background:linear-gradient(#5d4a3a,#c7bca8)"></div>
      <div class="thumb" role="img" aria-label="Stone bathtub" style="background:linear-gradient(#c8c6c2,#4a4c50)"></div>
      <div class="thumb" role="img" aria-label="Bathroom with window" style="background:linear-gradient(#4b3a2e,#bfb1a0)"></div>
      <div class="thumb" role="img" aria-label="Blue boiler unit" style="background:linear-gradient(#c9c9c9,#3e6aa8)"></div>
    </div>
    <div class="widgets">
      <div class="widget"><h3>&nbsp;</h3></div>
      <div class="widget"><h3>ARCHIVES</h3></div>
      <div class="widget"><h3>CATEGORIES</h3></div>
    </div>
  </main>

  <div class="arrow arrow-prev"><svg width="10" height="14" viewBox="0 0 10 14"><polyline points="8,1 2,7 8,13" fill="none" stroke="#999" stroke-width="3"/></svg></div>
  <div class="arrow arrow-next"><svg width="10" height="14" viewBox="0 0 10 14"><polyline points="2,1 8,7 2,13" fill="none" stroke="#999" stroke-width="3"/></svg></div>
</body>
</html>
```